Professional violinist needs business cards

I am trying to attract the following jobs:
-private violin lessons (primarily classical)
-performance gigs (weddings, birthday parties, funerals, etc.)
-collaborations with other artists (studio recordings, performances)

I want to communicate that I have a very high standard of excellence for my work, but I also love people and celebrations.
Values/style words I like are:
love, joy, peace, fun, beauty, authenticity, excellence, warmth, refined/sleek, free spirited. If that's too confusing, just ignore :)

I will attach my favorite business card template that I could find on Canva. The lines are supposed to be like a music staff, which I think is really cool, but I also don't want it to look too busy. I like the simple black and white--I think it looks sharp--but I also am open to other ideas. I also have seen business cards with pictures included that looked great, so I attached an image that could be used as well.

I am also attaching a file that I made of my initials that could be used as a logo, but I'm not sure if it should be included.

Information on the card:
-My name (18 letters total)
-"violinist"
-phone number, email, website

Thank you!

```html
<!DOCTYPE html>
<html lang="en">
<head>
<meta charset="utf-8">
<title>Clara Westonfield – Violinist Business Card</title>
<link href="https://fonts.googleapis.com/css2?family=Barlow+Condensed:wght@300;400;600&family=Barlow:wght@500;600&display=swap" rel="stylesheet">
<style>
  :root {
    --backdrop: #4b4c50;
    --backdrop-dark: #333438;
    --card-black: #050507;
    --card-white: #ffffff;
    --ink: #111111;
    --photo-light: #e9e9e9;
    --photo-mid: #8c8c8c;
    --photo-dark: #2a2a2a;
  }
  * { margin: 0; padding: 0; box-sizing: border-box; }
  html, body { width: 1200px; height: 1200px; overflow: hidden; }
  body {
    background: radial-gradient(circle at 60% 40%, var(--backdrop), var(--backdrop-dark));
    position: relative;
    font-family: "Barlow", sans-serif;
  }
  .card {
    position: absolute;
    left: 110px;
    width: 980px;
    height: 560px;
    box-shadow: 0 10px 30px rgba(0,0,0,0.45);
    overflow: hidden;
  }
  .card--back {
    top: 30px;
    background: var(--card-black);
    display: flex;
    align-items: center;
    justify-content: center;
    gap: 22px;
  }
  .back-mark {
    width: 26px; height: 26px; border-radius: 50%;
    background: var(--card-white);
  }
  .back-name {
    font-family: "Barlow Condensed", sans-serif;
    font-weight: 400;
    font-size: 64px;
    letter-spacing: 6px;
    color: var(--card-white);
    text-transform: uppercase;
  }
  .card--front {
    top: 610px;
    background: var(--card-white);
  }
  .portrait {
    position: absolute;
    right: 0; top: 0;
    width: 580px; height: 100%;
    background:
      linear-gradient(90deg, var(--card-white) 0%, rgba(255,255,255,0.6) 18%, rgba(255,255,255,0) 40%),
      linear-gradient(180deg, rgba(255,255,255,0) 70%, var(--card-white) 100%),
      linear-gradient(120deg, var(--photo-light) 0%, var(--photo-mid) 45%, var(--photo-dark) 75%, #111 100%);
  }
  .identity {
    position: absolute;
    left: 70px; top: 110px;
    display: flex;
    align-items: flex-start;
    gap: 22px;
  }
  .identity-mark {
    width: 16px; height: 16px; border-radius: 50%;
    background: var(--ink);
    margin-top: 20px;
  }
  .name {
    font-family: "Barlow Condensed", sans-serif;
    font-size: 52px;
    line-height: 1;
    color: var(--ink);
    text-transform: uppercase;
    font-weight: 400;
  }
  .name strong { font-weight: 600; }
  .role {
    font-family: "Barlow Condensed", sans-serif;
    font-weight: 300;
    font-size: 26px;
    letter-spacing: 12px;
    color: var(--ink);
    margin-top: 8px;
    padding-left: 170px;
  }
  .contacts {
    position: absolute;
    left: 150px; top: 270px;
    list-style: none;
  }
  .contact {
    display: flex;
    align-items: center;
    gap: 22px;
    height: 78px;
    font-weight: 600;
    font-size: 36px;
    color: var(--ink);
  }
  .contact svg { width: 38px; height: 38px; fill: var(--ink); flex: none; }
</style>
</head>
<body>
  <section class="card card--back" aria-label="Card back">
    <span class="back-mark"></span>
    <span class="back-name">Clara Westonfield</span>
  </section>

  <section class="card card--front" aria-label="Card front">
    <div class="portrait" role="img" aria-label="Black and white portrait of the violinist holding her violin beside a stone wall"></div>

    <div class="identity">
      <span class="identity-mark"></span>
      <div>
        <h1 class="name"><strong>Clara</strong> Westonfield</h1>
        <p class="role">VIOLINIST</p>
      </div>
    </div>

    <ul class="contacts">
      <li class="contact">
        <svg viewBox="0 0 24 24" aria-hidden="true"><path d="M6.6 10.8c1.4 2.8 3.8 5.1 6.6 6.6l2.2-2.2c.3-.3.7-.4 1-.2 1.1.4 2.3.6 3.6.6.6 0 1 .4 1 1V20c0 .6-.4 1-1 1C10.6 21 3 13.4 3 4c0-.6.4-1 1-1h3.5c.6 0 1 .4 1 1 0 1.3.2 2.5.6 3.6.1.3 0 .7-.2 1z"/></svg>
        <span>+00 5550 123 456</span>
      </li>
      <li class="contact">
        <svg viewBox="0 0 24 24" aria-hidden="true"><path d="M2 5h20v14H2zM3.5 6.5 12 13l8.5-6.5z" fill-rule="evenodd"/></svg>
        <span>clarawestonfield@mailbox.com</span>
      </li>
      <li class="contact">
        <svg viewBox="0 0 24 24" aria-hidden="true"><path d="M12 3 2 12h3v9h5v-6h4v6h5v-9h3z"/></svg>
        <span>www.clarawestonfield.com</span>
      </li>
    </ul>
  </section>
</body>
</html>
```